Rebrand & reskin fitbrisko.com (Uncoded)

Fitbrisko.com is a commerce website and app for sports and fitness classes and events. In order to improve its appeal, we invite designers to provide their 'skins' for the landing page, club page and event page. Designers can propose using alternate controls and layouts for these pages, and comment on ways to improve the site's usability. It must remain easy to use on a portrait mobile phone screen, responsive design where necessary to also provide a good experience on desktop.

Please navigate to fitbrisko.com and explore the site, and we look forwards to your suggestions!

Target Market(s)

Primary: Tech-savvy mobile users. Secondary: Desktop users

Industry/Entity Type

Health And Wellness

Number of Pages Required

3 page

Font styles to use
Sans Serif

Colors
ffffff
f37122

Requirements
Must have
• This brief is all about changing the look and feel of the site; the winning design will have an immediate 'wow' factor, yet not sacrifice the ease of finding and paying for classes. It must retain the logo, white and orange must be the primary colours used.
Should not have
• The colour palette must remain roughly as is; for example, a very dark site will not appeal.

```html
<!DOCTYPE html>
<html lang="en">
<head>
<meta charset="utf-8">
<title>Fitbrisko – Feed</title>
<link href="https://fonts.googleapis.com/css2?family=Roboto:wght@400;500;700&display=swap" rel="stylesheet">
<style>
:root{
  --orange:#f37122;
  --white:#ffffff;
  --ink:#333333;
  --muted:#777777;
  --side:#262626;
  --side-line:#1a1a1a;
  --tile:#8a8a8a;
  --tile-dark:#2a2a2a;
  --footer:#050505;
  --line:#e3e3e3;
}
*{box-sizing:border-box;margin:0;padding:0}
html,body{width:1200px;height:1034px;overflow:hidden}
body{font-family:'Roboto',sans-serif;background:var(--white);position:relative;color:var(--ink)}
.site-header{position:absolute;left:0;top:0;width:1200px;height:103px;background:var(--white)}
.brand{position:absolute;left:94px;top:36px;display:flex;align-items:center;gap:10px;color:var(--orange);font-weight:700;font-size:28px;letter-spacing:1px}
.brand-mark{width:30px;height:30px;border-radius:50%;background:var(--orange)}
.main-nav{position:absolute;top:0;left:528px;display:flex;height:103px}
.main-nav a{display:flex;align-items:center;padding:0 20px;font-size:15px;color:#444;text-decoration:none;letter-spacing:.3px}
.main-nav a.active{background:var(--orange);color:var(--white);width:81px;justify-content:center;padding:0}
.stage{position:absolute;left:0;top:103px;width:1200px;height:823px;
  background:radial-gradient(ellipse at 50% 20%,#3c4e6a 0%,#1b2538 45%,#0e1522 60%),#111;}
.stage::after{content:"";position:absolute;left:0;right:0;bottom:0;height:330px;background:linear-gradient(to bottom,rgba(60,90,40,0),#4c7a2c 45%,#5d8a34)}
.sidebar{position:absolute;left:88px;top:142px;width:228px;height:747px;background:var(--side);z-index:2}
.side-item{display:flex;height:45px;border-bottom:1px solid var(--side-line);color:var(--white);font-size:16px;align-items:center}
.side-item .ico{width:63px;height:100%;display:flex;align-items:center;justify-content:center;border-right:1px solid var(--side-line)}
.side-item .label{flex:1;padding-left:14px}
.side-item .chev{padding-right:16px}
.side-item.active{background:var(--orange);border-color:var(--orange)}
.side-item.active .ico{border-right-color:#d96419}
.banner{position:absolute;left:349px;top:142px;width:764px;height:267px;border:4px solid var(--white);z-index:2;
  background:linear-gradient(180deg,#2d4a78 0%,#3a5a85 45%,#5b7340 80%,#6d8a3e 100%);
  display:flex;flex-direction:column;align-items:center;justify-content:center;color:var(--white);text-align:center}
.banner h1{font-size:33px;font-weight:700;letter-spacing:-.3px;margin-top:-20px}
.banner p{font-size:15px;line-height:21px;margin-top:8px}
.panel{position:absolute;top:432px;height:457px;background:var(--white);z-index:2}
.panel-head{height:47px;background:var(--orange);color:var(--white);font-size:18px;font-weight:500;display:flex;align-items:center;padding-left:21px}
.classes{left:349px;width:418px}
.class-row{display:flex;height:100px;border-bottom:1px solid var(--line);padding:22px 0 0 19px}
.class-row:last-child{border-bottom:0}
.badge{width:64px;height:64px;border-radius:4px;flex:none}
.badge.red{background:#7d1419}
.badge.black{background:#202020}
.class-info{margin-left:16px;font-size:11px}
.class-info .club{color:var(--orange);font-size:11px;margin-top:6px}
.class-info .desc{color:#444;margin-top:7px}
.class-info .when{margin-top:8px;display:flex;align-items:center;gap:8px;color:#333}
.events{left:780px;width:334px}
.event-row{display:flex;height:100px;border-bottom:1px solid var(--line);padding:17px 0 0 20px}
.event-row:last-child{border-bottom:0}
.date{width:40px;height:82px;flex:none;display:flex;flex-direction:column;color:var(--white);text-align:center}
.date .top{background:var(--tile);height:40px;padding-top:4px;font-size:16px;line-height:16px}
.date .top small{display:block;font-size:8px;margin-top:4px}
.date .yr{background:var(--tile-dark);flex:1;font-size:12px;display:flex;align-items:center;justify-content:center}
.event-info{margin-left:14px;width:244px}
.event-info h3{font-size:12.5px;font-weight:400;color:#333;margin-top:1px}
.event-info p{font-size:10.5px;color:var(--muted);line-height:16.5px;margin-top:4px;text-align:justify}
.event-info a{font-size:11px;color:var(--orange);text-decoration:none}
.site-footer{position:absolute;left:0;top:926px;width:1200px;height:108px;background:var(--footer);color:var(--white)}
.foot-links{position:absolute;left:98px;top:32px;font-size:14px}
.foot-links span{margin:0 7px}
.copy{position:absolute;left:99px;top:59px;font-size:14px}
.social{position:absolute;left:944px;top:36px;display:flex;gap:8px}
.social i{width:35px;height:35px;border-radius:3px;display:block}
</style>
</head>
<body>
<header class="site-header">
  <div class="brand"><span class="brand-mark"></span>FITBRISKO</div>
  <nav class="main-nav">
    <a href="#">CALENDAR</a><a href="#" class="active">FEED</a><a href="#">NEARBY</a><a href="#">SPORTS</a><a href="#">FITNESS</a><a href="#">EVENTS</a>
  </nav>
</header>

<main class="stage" role="img" aria-label="Floodlit stadium with green sports pitch"></main>

<aside class="sidebar">
  <div class="side-item active"><span class="ico"><svg width="16" height="16" viewBox="0 0 16 16" fill="#fff"><rect x="1" y="1" width="9" height="11"/><rect x="6" y="5" width="9" height="10" fill="none" stroke="#fff" stroke-width="2"/></svg></span><span class="label">My Diary</span><span class="chev">›</span></div>
  <div class="side-item"><span class="ico"><svg width="17" height="14" viewBox="0 0 17 14" fill="#fff"><path d="M8.5 0L0 7h2.5v7h4V9h4v5h4V7H17z"/></svg></span><span class="label">My Clubs</span><span class="chev">›</span></div>
  <div class="side-item"><span class="ico"><svg width="14" height="16" viewBox="0 0 14 16" fill="#fff"><circle cx="7" cy="4" r="4"/><path d="M0 16c0-5 3-7 7-7s7 2 7 7z"/></svg></span><span class="label">My Profile</span><span class="chev">›</span></div>
  <div class="side-item"><span class="ico"><svg width="18" height="14" viewBox="0 0 18 14" fill="#fff"><path d="M0 5h6V1l6 6-6 6V9H0z"/><path d="M11 1h6v12h-6" fill="none" stroke="#fff" stroke-width="2"/></svg></span><span class="label">Login</span><span class="chev">›</span></div>
</aside>

<section class="banner" role="img" aria-label="Sprinter running on a stadium track">
  <h1>WELCOME TO FITBRISKO</h1>
  <p>Thanks for visiting! Here are a list of events that we hope are of interest.<br>Just click on the grey tick to join an event, or Login</p>
</section>

<section class="panel classes">
  <div class="panel-head">SPORTS AND FITNESS CLASSES</div>
  <div class="class-row"><span class="badge red"></span><div class="class-info"><div class="club">RIVERSIDE HARRIERS @ OAKFIELD SCHOOL</div><div class="desc">Freestyle (crawl) training comprising of warm up, drills and</div><div class="when"><svg width="10" height="10" viewBox="0 0 10 10" fill="#f37122"><rect y="2" width="10" height="8"/></svg>MONDAY&nbsp; 20/01/2016</div></div></div>
  <div class="class-row"><span class="badge black"></span><div class="class-info"><div class="club">RIVERSIDE HARRIERS @ OAKFIELD SCHOOL</div><div class="desc">Freestyle (crawl) training comprising of warm up, drills and</div><div class="when"><svg width="10" height="10" viewBox="0 0 10 10" fill="#f37122"><rect y="2" width="10" height="8"/></svg>MONDAY&nbsp; 20/01/2016</div></div></div>
  <div class="class-row"><span class="badge red"></span><div class="class-info"><div class="club">RIVERSIDE HARRIERS @ OAKFIELD SCHOOL</div><div class="desc">Freestyle (crawl) training comprising of warm up, drills and</div><div class="when"><svg width="10" height="10" viewBox="0 0 10 10" fill="#f37122"><rect y="2" width="10" height="8"/></svg>MONDAY&nbsp; 20/01/2016</div></div></div>
  <div class="class-row"><span class="badge black"></span><div class="class-info"><div class="club">RIVERSIDE HARRIERS @ OAKFIELD SCHOOL</div><div class="desc">Freestyle (crawl) training comprising of warm up, drills and</div><div class="when"><svg width="10" height="10" viewBox="0 0 10 10" fill="#f37122"><rect y="2" width="10" height="8"/></svg>MONDAY&nbsp; 20/01/2016</div></div></div>
</section>

<section class="panel events">
  <div class="panel-head">EVENTS</div>
  <div class="event-row"><div class="date"><div class="top">02<small>JUN</small></div><div class="yr">2016</div></div><div class="event-info"><h3>RIVERSIDE HARRIERS</h3><p>Lorem Ipsum has been the industry's standard dummy text ver since the 1500s, when unknown</p><a href="#">View More »</a></div></div>
  <div class="event-row"><div class="date"><div class="top">02<small>JUN</small></div><div class="yr">2016</div></div><div class="event-info"><h3>RIVERSIDE HARRIERS</h3><p>Lorem Ipsum has been the industry's standard dummy text ver since the 1500s, when unknown</p><a href="#">View More »</a></div></div>
  <div class="event-row"><div class="date"><div class="top">02<small>JUN</small></div><div class="yr">2016</div></div><div class="event-info"><h3>RIVERSIDE HARRIERS</h3><p>Lorem Ipsum has been the industry's standard dummy text ver since the 1500s, when unknown</p><a href="#">View More »</a></div></div>
  <div class="event-row"><div class="date"><div class="top">02<small>JUN</small></div><div class="yr">2016</div></div><div class="event-info"><h3>RIVERSIDE HARRIERS</h3><p>Lorem Ipsum has been the industry's standard dummy text ver since the 1500s, when unknown</p><a href="#">View More »</a></div></div>
</section>

<footer class="site-footer">
  <div class="foot-links">Privacy Policy<span>|</span>Terms of Use<span>|</span>About Us<span>|</span>Sitemap</div>
  <div class="copy">Copyright © 2016&nbsp; All Rights</div>
  <div class="social"><i style="background:#2aa3e0"></i><i style="background:#d0302a"></i><i style="background:#3b5a9a"></i><i style="background:#1a7ac0"></i></div>
</footer>
</body>
</html>
```